BildeVOLD buisnesscard

Hey :) I need a modern buisnesscard for my company BildeVOLD
It most have:
Dagligleder og Fotograf: Henrik Audun Strandvik

Mob: +4791264085
Epost: post@bildevold.example
Adresse: Kvernbakken9, 6040 Langevåg

Facbook and instagram logo with text BildeVOLD

BildeVOLD logo

It Company

```html
<!DOCTYPE html>
<html lang="no">
<head>
<meta charset="utf-8">
<title>BildeVOLD – visittkort</title>
<link rel="stylesheet" href="https://fonts.googleapis.com/css2?family=Open+Sans:wght@400;600;700;800&display=swap">
<style>
  :root {
    --bg: #e9eaec;
    --card: #ffffff;
    --blue: #2a82b8;
    --blue-back: #2b83b9;
    --blue-faint: #4a97c6;
    --pink: #d63d8f;
    --ink: #555a60;
    --white: #ffffff;
  }
  * { margin: 0; padding: 0; box-sizing: border-box; }
  html, body {
    width: 1105px; height: 1200px; overflow: hidden;
    background: var(--bg);
    font-family: "Open Sans", Arial, sans-serif;
  }
  .card {
    position: absolute; left: 192px;
    width: 720px; height: 410px;
    overflow: hidden;
  }
  /* Front */
  .card-front { top: 150px; background: var(--card); }
  .name-marker {
    position: absolute; left: 0; top: 50px;
    width: 16px; height: 52px; background: var(--blue);
  }
  .holder-name {
    position: absolute; left: 45px; top: 46px;
    font-size: 25px; font-weight: 600; color: var(--blue);
  }
  .holder-role {
    position: absolute; left: 45px; top: 82px;
    font-size: 18px; color: var(--pink);
  }
  .address {
    position: absolute; left: 45px; top: 214px;
    font-size: 18px; line-height: 27px; color: var(--ink);
  }
  .contact-list {
    position: absolute; left: 45px; top: 292px;
    list-style: none;
    font-size: 18px; line-height: 28px; color: var(--ink);
  }
  .contact-list li { display: flex; align-items: center; gap: 10px; }
  .contact-list svg { width: 18px; height: 18px; flex: none; }
  .front-wordmark {
    position: absolute; right: 40px; top: 318px;
    font-size: 44px; font-weight: 800; color: var(--blue);
    letter-spacing: -0.5px;
  }
  .front-band { position: absolute; left: 0; bottom: 0; width: 720px; height: 14px; }

  /* Back */
  .card-back { top: 640px; background: var(--blue-back); }
  .back-decoration {
    position: absolute; left: 20px; top: 150px;
    font-size: 92px; font-weight: 800; color: var(--blue-faint);
    letter-spacing: -2px; white-space: nowrap;
  }
  .back-wordmark {
    position: absolute; left: 608px; top: 205px;
    transform: translate(-50%, -50%) rotate(-90deg);
    font-size: 56px; font-weight: 800; color: var(--white);
    white-space: nowrap; letter-spacing: -0.5px;
  }
  .social-rail { position: absolute; left: 640px; top: 60px; width: 40px; height: 290px; }
</style>
</head>
<body>

<section class="card card-front" aria-label="Visittkort forside">
  <span class="name-marker"></span>
  <h1 class="holder-name">Henrik Audun Strandvik</h1>
  <p class="holder-role">Dagligleder og Fotograf</p>

  <address class="address">Kvernbakken9<br>6040 Langevåg</address>

  <ul class="contact-list">
    <li>
      <svg viewBox="0 0 18 18"><rect x="4" y="1" width="10" height="16" rx="2" fill="none" stroke="var(--blue)" stroke-width="2"/><rect x="7" y="13" width="4" height="1.6" fill="var(--blue)"/></svg>
      +4791264085
    </li>
    <li>
      <svg viewBox="0 0 18 18"><rect x="1" y="4" width="16" height="11" fill="var(--blue)"/><path d="M1 4 L9 10 L17 4" fill="none" stroke="#fff" stroke-width="1.5"/></svg>
      post@bildevold.example
    </li>
    <li>
      <svg viewBox="0 0 18 18"><circle cx="9" cy="9" r="8" fill="var(--blue)"/><path d="M1 9 H17 M9 1 C5 5 5 13 9 17 M9 1 C13 5 13 13 9 17" fill="none" stroke="#fff" stroke-width="1.1"/></svg>
      www.bildevold.example
    </li>
  </ul>

  <div class="front-wordmark">BildeVOLD</div>

  <svg class="front-band" viewBox="0 0 720 14" preserveAspectRatio="none">
    <rect x="0" y="0" width="720" height="14" fill="var(--blue)"/>
    <polygon points="530,0 720,0 720,14 545,14" fill="var(--pink)"/>
    <polygon points="520,0 527,0 542,14 535,14" fill="var(--card)"/>
  </svg>
</section>

<section class="card card-back" aria-label="Visittkort bakside">
  <div class="back-decoration" aria-hidden="true">BildeVOLD</div>
  <div class="back-wordmark">BildeVOLD</div>
  <svg class="social-rail" viewBox="0 0 40 290">
    <line x1="20" y1="0" x2="20" y2="104" stroke="var(--white)" stroke-width="1.5" opacity="0.8"/>
    <circle cx="20" cy="120" r="14" fill="none" stroke="var(--white)" stroke-width="2"/>
    <circle cx="20" cy="165" r="14" fill="none" stroke="var(--white)" stroke-width="2"/>
    <line x1="20" y1="181" x2="20" y2="290" stroke="var(--white)" stroke-width="1.5" opacity="0.8"/>
  </svg>
</section>

</body>
</html>
```